Quillmere Supply Chain and Logistic Consulting

Please review the attached Business Card. I want as close to this card with the colors, fonts, and quality of the card as possible. The attached compass should replace the deer head on both sides of the card and the text should say:

Backside
Compass JPEG
Quillmere
A Supply Chain and Logistics Consulting Company

Frontside
Quillmere
Ray Falkner - Port Veldon
President
____________________________________
(555) 314-9027
QuillmereSCL@Examplemail.com
_____________________________________

Bottom Front Side

Target Market(s)

Businesses

Contact Information for Business Card

Backside
Compass JPEG
Quillmere

Frontside
Quillmere
President
(555) 314-9027
QuillmereSCL@Examplemail.com

Bottom Front Side

Font styles to use
Serif
Script

Colors

Designer to choose colors to be used in the design.

Requirements
Must have
• See attached card for reference
Nice to have
Should not have

```html
<!DOCTYPE html>
<html lang="en">
<head>
<meta charset="utf-8">
<title>Quillmere Business Card</title>
<link rel="stylesheet" href="https://fonts.googleapis.com/css2?family=Cormorant+SC:wght@500&family=Tinos:wght@400;700&display=swap">
<style>
  :root {
    --stage: #3a3a3a;
    --card: #262626;
    --card-edge: #1c1c1c;
    --silver: #e9e9e9;
    --silver-soft: #bdbdbd;
    --rule: #6a6a6a;
    --mark: #d6d6d6;
  }
  * { margin: 0; padding: 0; box-sizing: border-box; }
  html, body { width: 1200px; height: 782px; overflow: hidden; }
  body {
    background: var(--stage);
    display: flex;
    flex-direction: column;
    align-items: center;
    justify-content: center;
    gap: 36px;
  }
  .card {
    width: 560px;
    height: 320px;
    background: var(--card);
    border: 1px solid var(--card-edge);
    box-shadow: 0 8px 22px rgba(0,0,0,0.45);
    position: relative;
    display: flex;
    flex-direction: column;
    align-items: center;
    color: var(--silver);
    text-align: center;
  }
  .wordmark {
    font-family: "Tinos", serif;
    font-weight: 400;
    letter-spacing: 0.08em;
    color: var(--silver);
  }
  .tagline {
    font-family: "Cormorant SC", serif;
    font-weight: 500;
    font-size: 17px;
    letter-spacing: 0.08em;
    color: var(--silver-soft);
  }

  /* Back side */
  .card-back { justify-content: center; padding-top: 10px; }
  .card-back .mark-circle { width: 118px; height: 118px; margin-bottom: 18px; }
  .card-back .wordmark { font-size: 27px; margin-bottom: 8px; }

  /* Front side */
  .card-front { padding-top: 30px; }
  .card-front .wordmark { font-size: 38px; margin-bottom: 16px; }
  .contact { font-family: "Tinos", serif; line-height: 1.2; }
  .contact-name { font-weight: 700; font-size: 20px; color: var(--silver); }
  .contact-role { font-size: 16px; color: var(--silver-soft); margin-bottom: 6px; }
  .contact-rule {
    width: 250px; height: 1px; margin: 4px auto;
    background: linear-gradient(90deg, transparent, var(--rule), transparent);
  }
  .contact-line { font-size: 16px; color: var(--silver); }
  .card-front .tagline { position: absolute; bottom: 22px; left: 0; right: 0; }
</style>
</head>
<body>
  <section class="card card-back" aria-label="Back of business card">
    <svg class="mark-circle" viewBox="0 0 118 118" aria-hidden="true">
      <circle cx="59" cy="59" r="56" fill="none" stroke="var(--mark)" stroke-width="2"/>
    </svg>
    <div class="wordmark">QUILLMERE</div>
    <div class="tagline">A Supply Chain and Logistics Consulting Company</div>
  </section>

  <section class="card card-front" aria-label="Front of business card">
    <div class="wordmark">QUILLMERE</div>
    <div class="contact">
      <div class="contact-name">Ray Falkner - Port Veldon</div>
      <div class="contact-role">President</div>
      <div class="contact-rule"></div>
      <div class="contact-line">(555) 314-9027</div>
      <div class="contact-line">QuillmereSCL@Examplemail.com</div>
      <div class="contact-rule"></div>
    </div>
    <div class="tagline">A Supply Chain and Logistics Consulting Company</div>
  </section>
</body>
</html>
```